Vehicle Rental Hire in the Algarve - Portugal

We are opening a Vehicle Rental company in the Algarve - Portugal - this will attract both locals and Tourists visiting. So we want this website to capture the beautiful location we will be set in, along with the familiarity of a vehicle rental company. And to keep a colour scheme in Line with out Logo. We are Quenmira Vehicle Rental.

Industry/Entity Type

Vehicle Rental

Number of Pages Required

1 page

Requirements
Must have
• must be professional, and simple to use navigation bar - must also have a "make a reservation" box - similar to the screenshot attached - Under our logo it must read "Vehicle Rental"
Nice to have
• It needs to be in a colour scheme that fits in with our logo

```html
<!DOCTYPE html>
<html lang="en">
<head>
<meta charset="utf-8">
<title>Quenmira Vehicle Rental</title>
<link href="https://fonts.googleapis.com/css2?family=Lato:wght@400;700&family=Yellowtail&display=swap" rel="stylesheet">
<style>
:root{
  --blue:#2a1fdc;
  --red:#c5302b;
  --ink:#333;
  --muted:#555;
  --white:#fff;
}
*{box-sizing:border-box;margin:0;padding:0}
html,body{width:1200px;height:3420px;overflow:hidden}
body{position:relative;font-family:'Lato',sans-serif;color:var(--ink);background:var(--white)}
.abs{position:absolute}
.script{font-family:'Yellowtail',cursive;color:var(--blue);font-weight:400;white-space:nowrap}

/* top bar & header */
.topbar{left:429px;top:0;width:771px;height:42px;background:var(--blue);border-bottom-left-radius:22px;color:var(--white);font-size:16px}
.topbar .item{position:absolute;top:11px;display:flex;align-items:center;gap:9px;white-space:nowrap}
.logo-disc{left:117px;top:-13px;width:186px;height:186px;border-radius:50%;background:var(--white);z-index:3;display:flex;align-items:center;justify-content:center}
.logo-disc .ring{width:148px;height:148px;border:2px solid var(--blue);border-radius:50%;display:flex;flex-direction:column;align-items:center;justify-content:center;margin-top:14px}
.logo-name{font-size:24px;font-weight:700;color:var(--blue);letter-spacing:.5px}
.logo-sub{font-size:12px;font-weight:700;color:var(--red);margin-top:2px}
.nav{top:72px;font-size:17px;color:#222;white-space:nowrap}
.nav.active{color:var(--red);border-bottom:2px solid var(--red);padding-bottom:2px}

/* hero */
.hero{left:0;top:120px;width:1200px;height:600px;background:linear-gradient(180deg,#5d7277 0%,#8ea3a5 38%,#a5aba5 55%,#6f7068 75%,#55544f 100%)}
.hero-disc{left:609px;top:166px;width:504px;height:504px;border-radius:50%;background:var(--red);color:var(--white);text-align:center}
.hero-disc .welcome{position:absolute;left:0;width:100%;top:148px;font-family:'Yellowtail',cursive;font-size:50px;line-height:60px}
.hero-disc .hero-title{position:absolute;left:0;width:100%;top:222px;font-size:40px;line-height:50px;font-weight:700;white-space:nowrap}
.hero-btn{position:absolute;left:167px;top:306px;width:172px;height:38px;border-radius:19px;background:var(--white);color:var(--red);font-size:15px;line-height:38px}

/* reservation */
.res-tab{left:111px;top:680px;width:239px;height:42px;background:var(--blue);color:var(--white);font-size:21px;font-weight:700;padding:9px 0 0 21px;white-space:nowrap}
.res-box{left:111px;top:720px;width:977px;height:222px;background:var(--blue)}
.label{color:var(--white);font-size:15px;font-weight:700;white-space:nowrap}
.field{width:170px;height:42px;background:var(--white);border:1px solid #ccc;font-size:11px;color:#555;padding:0 12px;display:flex;align-items:center;justify-content:space-between}
.check{left:139px;top:846px;color:var(--white);font-size:14px;display:flex;align-items:center;gap:8px;white-space:nowrap}
.check .box{width:14px;height:14px;background:var(--white);border-radius:2px;display:flex;align-items:center;justify-content:center}
.search-btn{left:893px;top:878px;width:170px;height:39px;border-radius:20px;background:var(--red);color:var(--white);font-size:15px;font-weight:700;text-align:center;line-height:39px}

/* about */
.about-band{left:0;top:942px;width:1200px;height:628px;background:linear-gradient(180deg,#e9ecf1 0%,#f2f1ee 60%,#f6f4f0 100%)}
.about-photo{left:114px;top:1030px;width:444px;height:444px;border-radius:50%;background:linear-gradient(180deg,#3d5f9c 0%,#7f9fc7 38%,#b39a7a 52%,#6d5a49 62%,#2e3b56 80%,#8a6a3c 100%);overflow:hidden}
.about-title{left:617px;top:1020px;font-size:52px;line-height:70px}
.about-text{left:617px;top:1104px;width:471px;font-size:14.5px;line-height:25px;color:var(--muted)}
.about-text p+p{margin-top:23px}
.btn-red{height:33px;border-radius:17px;background:var(--red);color:var(--white);font-size:13px;font-weight:700;text-align:center;line-height:33px}

/* services */
.section-title{width:1200px;left:0;text-align:center;font-size:52px;line-height:70px}
.svc-img{top:1750px;width:304px;height:199px}
.svc-title{top:1966px;width:304px;text-align:center;color:var(--blue);font-size:22px;font-weight:700;white-space:nowrap}
.svc-text{top:2004px;width:304px;text-align:center;color:var(--muted);font-size:14.5px;line-height:26px;padding:0 20px}

/* features */
.features{left:0;top:2223px;width:1200px;height:368px;background:linear-gradient(180deg,#3a32d2 0%,#2c27c4 40%,#2a2ab8 70%,#3437c6 100%)}
.feat-icon{top:2299px;width:106px;height:106px;border-radius:50%;background:var(--white);border:3px solid #f3d4d2;display:flex;align-items:center;justify-content:center}
.feat-title{top:2425px;width:240px;text-align:center;color:var(--white);font-size:21px;font-weight:700;white-space:nowrap}
.feat-text{top:2461px;width:240px;text-align:center;color:var(--white);font-size:14.5px;line-height:22px;padding:0 18px}

/* partners */
.partner{top:2775px;height:64px;border-radius:8px;background:#d8d9e3}

/* footer */
.footer{left:0;top:2987px;width:1200px;height:433px;background:linear-gradient(180deg,#16171d 0%,#0f1016 60%,#15151a 100%)}
.foot-logo{left:136px;top:3059px;width:152px;height:152px;border:2px solid var(--white);border-radius:50%;display:flex;flex-direction:column;align-items:center;justify-content:center;color:var(--white)}
.foot-logo .n{font-size:26px;font-weight:700}
.foot-logo .s{font-size:12px;margin-top:2px}
.social{top:3247px;width:20px;height:20px;border-radius:3px;background:var(--white)}
.foot-h{top:3056px;font-size:21px;font-weight:700;color:var(--white)}
.foot-list{top:3118px;list-style:none;font-size:15px;line-height:34px;color:var(--white)}
.foot-sub{left:850px;top:3116px;width:240px;font-size:14.5px;line-height:30px;color:var(--white)}
.email{left:850px;top:3195px;width:199px;height:35px;background:var(--white);color:#777;font-size:12px;padding:0 13px;line-height:35px}
.send{left:1049px;top:3195px;width:39px;height:35px;background:var(--blue);display:flex;align-items:center;justify-content:center}
.foot-line{left:111px;top:3365px;width:977px;height:1px;background:#bbb}
.copy{left:0;top:3385px;width:1200px;text-align:center;font-size:13px;color:var(--white)}
</style>
</head>
<body>

<!-- header -->
<div class="abs topbar">
  <span class="item" style="left:110px">
    <svg width="16" height="16" viewBox="0 0 24 24"><path fill="#fff" d="M6.6 10.8a15 15 0 0 0 6.6 6.6l2.2-2.2c.3-.3.7-.4 1-.2 1.1.4 2.3.6 3.6.6.6 0 1 .4 1 1V20c0 .6-.4 1-1 1A17 17 0 0 1 3 4c0-.6.4-1 1-1h3.5c.6 0 1 .4 1 1 0 1.3.2 2.5.6 3.6.1.3 0 .7-.2 1z"/></svg>
    +351 289 000 000
  </span>
  <span class="item" style="left:329px">
    <svg width="17" height="14" viewBox="0 0 24 18"><rect x="0" y="0" width="24" height="18" rx="2" fill="#fff"/><path d="M1 1l11 9 11-9" stroke="#2a1fdc" stroke-width="2" fill="none"/></svg>
    info@quenmira-rental.pt
  </span>
  <span class="item" style="left:640px">
    <svg width="16" height="16" viewBox="0 0 24 24"><circle cx="10" cy="10" r="7" stroke="#fff" stroke-width="3" fill="none"/><path d="M15 15l6 6" stroke="#fff" stroke-width="3.5" stroke-linecap="round"/></svg>
  </span>
</div>
<div class="abs logo-disc">
  <div class="ring">
    <span class="logo-name">QUENMIRA</span>
    <span class="logo-sub">Vehicle Rental</span>
  </div>
</div>
<span class="abs nav active" style="left:373px">Home</span>
<span class="abs nav" style="left:492px">About Us</span>
<span class="abs nav" style="left:634px">Services</span>
<span class="abs nav" style="left:770px">Partners</span>
<span class="abs nav" style="left:907px">Team</span>
<span class="abs nav" style="left:1020px">Contacts</span>

<!-- hero -->
<div class="abs hero" role="img" aria-label="White SUV driving on a coastal road under a cloudy sky"></div>
<div class="abs hero-disc">
  <svg class="abs" style="left:0;top:0" width="504" height="504" viewBox="0 0 504 504">
    <path d="M33 186 A224 224 0 0 1 471 186" stroke="#fff" stroke-width="3" fill="none"/>
    <path d="M40 338 A224 224 0 0 0 464 338" stroke="#fff" stroke-width="3" fill="none"/>
  </svg>
  <div class="welcome">Welcome To</div>
  <div class="hero-title">Quenmira Vehicle Rental</div>
  <div class="hero-btn">Contact Us</div>
</div>

<!-- reservation -->
<div class="abs res-tab">Make a Reservation</div>
<div class="abs res-box"></div>
<span class="abs label" style="left:140px;top:748px">Pick Up Location</span>
<span class="abs label" style="left:329px;top:748px">Driver's age</span>
<span class="abs label" style="left:517px;top:748px">Vehicle Category</span>
<span class="abs label" style="left:706px;top:748px">Pick Up Date</span>
<span class="abs label" style="left:894px;top:748px">Drop Off Date</span>
<div class="abs field" style="left:139px;top:780px">Please Choose.... <svg width="12" height="8" viewBox="0 0 12 8"><path d="M1 1l5 5 5-5" stroke="#222" stroke-width="2" fill="none"/></svg></div>
<div class="abs field" style="left:328px;top:780px">Please Choose.... <svg width="12" height="8" viewBox="0 0 12 8"><path d="M1 1l5 5 5-5" stroke="#222" stroke-width="2" fill="none"/></svg></div>
<div class="abs field" style="left:516px;top:780px">All <svg width="12" height="8" viewBox="0 0 12 8"><path d="M1 1l5 5 5-5" stroke="#222" stroke-width="2" fill="none"/></svg></div>
<div class="abs field" style="left:705px;top:780px">dd-mm-aaaa</div>
<div class="abs field" style="left:893px;top:780px">dd-mm-aaaa</div>
<div class="abs check"><span class="box"><svg width="10" height="10" viewBox="0 0 10 10"><path d="M1 5l3 3 5-7" stroke="#2a1fdc" stroke-width="2" fill="none"/></svg></span>Pick up location same as return location</div>
<span class="abs label" style="left:517px;top:845px">Hour</span>
<span class="abs label" style="left:706px;top:845px">Hour</span>
<div class="abs field" style="left:516px;top:876px">8:00 <svg width="12" height="8" viewBox="0 0 12 8"><path d="M1 1l5 5 5-5" stroke="#222" stroke-width="2" fill="none"/></svg></div>
<div class="abs field" style="left:705px;top:876px">8:00 <svg width="12" height="8" viewBox="0 0 12 8"><path d="M1 1l5 5 5-5" stroke="#222" stroke-width="2" fill="none"/></svg></div>
<div class="abs search-btn">Search</div>

<!-- about -->
<div class="abs about-band" role="img" aria-label="Faint view of a white coastal town on the Algarve cliffs"></div>
<div class="abs about-photo" role="img" aria-label="Riverside city with an iron arch bridge">
  <svg class="abs" style="left:0;top:0" width="444" height="444" viewBox="0 0 444 444">
    <path d="M30 165 A200 200 0 0 1 414 165" stroke="#fff" stroke-width="3" fill="none"/>
    <path d="M34 290 A200 200 0 0 0 410 290" stroke="#fff" stroke-width="3" fill="none"/>
  </svg>
</div>
<h2 class="abs script about-title">About Us</h2>
<div class="abs about-text">
  <p>Lorem ipsum dolor sit amet, consectetur adipiscing elit, sed do eiusmod tempor incididunt ut labore et dolore magna aliqua. Ut enim ad minim veniam, quis nostrud exercitation ullamco laboris nisi ut aliquip ex ea commodo consequat. Duis aute irure dolor in reprehenderit in voluptate velit esse cillum dolore eu fugiat nulla pariatur. Excepteur sint occaecat cupidatat non proident, sunt in culpa qui officia deserunt mollit anim id est laborum.</p>
  <p>Sed ut perspiciatis unde omnis iste natus error sit voluptatem accusantium doloremque laudantium, totam rem aperiam, eaque ipsa quae ab illo inventore veritatis et quasi architecto beatae vitae dicta sunt explicabo.</p>
</div>
<div class="abs btn-red" style="left:617px;top:1437px;width:151px">Read More</div>

<!-- services -->
<h2 class="abs script section-title" style="top:1645px">Our Services</h2>
<div class="abs svc-img" style="left:113px;background:linear-gradient(135deg,#6f7b86,#c9cdd2 55%,#8f8a84)" role="img" aria-label="Hands signing a rental agreement on a clipboard beside parked cars"></div>
<div class="abs svc-img" style="left:449px;background:linear-gradient(135deg,#3e4752,#8a7565 50%,#d9dbdd)" role="img" aria-label="Customer in a car receiving the keys"></div>
<div class="abs svc-img" style="left:783px;background:linear-gradient(135deg,#d8d9da,#9fa3a8 45%,#c2413e 80%,#e5e5e5)" role="img" aria-label="Row of rental cars parked in a lot"></div>
<div class="abs svc-title" style="left:113px">Lorem ipsum dolor sit</div>
<div class="abs svc-title" style="left:449px">Sed ut perspiciatis unde</div>
<div class="abs svc-title" style="left:783px">Nemo ipsam voluptatem</div>
<div class="abs svc-text" style="left:113px">Excepteur sint occaecat cupidatat non proident, sunt in culpa qui officia deserunt mollit anim id est laborum.</div>
<div class="abs svc-text" style="left:449px">Excepteur sint occaecat cupidatat non proident, sunt in culpa qui officia deserunt mollit anim id est laborum.</div>
<div class="abs svc-text" style="left:783px">Excepteur sint occaecat cupidatat non proident, sunt in culpa qui officia deserunt mollit anim id est laborum.</div>
<div class="abs btn-red" style="left:190px;top:2103px;width:151px">Read More</div>
<div class="abs btn-red" style="left:525px;top:2103px;width:151px">Read More</div>
<div class="abs btn-red" style="left:860px;top:2103px;width:151px">Read More</div>

<!-- features -->
<div class="abs features" role="img" aria-label="Blue-tinted view of Algarve coastal cliffs"></div>
<div class="abs feat-icon" style="left:149px">
  <svg width="56" height="56" viewBox="0 0 24 24"><circle cx="12" cy="12" r="10" stroke="#c5302b" stroke-width="1.6" fill="none" stroke-dasharray="50 8"/><text x="12" y="15" font-family="Lato,sans-serif" font-weight="700" font-size="8" fill="#c5302b" text-anchor="middle">24</text></svg>
</div>
<div class="abs feat-icon" style="left:406px">
  <svg width="52" height="52" viewBox="0 0 24 24"><rect x="3" y="3" width="18" height="7" rx="2" fill="#c5302b"/><rect x="9.5" y="11" width="5" height="10" rx="2" fill="#c5302b"/></svg>
</div>
<div class="abs feat-icon" style="left:665px">
  <svg width="50" height="50" viewBox="0 0 24 24"><path d="M7 11V7a5 5 0 0 1 10 0v4" stroke="#c5302b" stroke-width="2" fill="none"/><rect x="5" y="11" width="14" height="10" rx="2" fill="#c5302b"/><circle cx="12" cy="16" r="1.6" fill="#fff"/></svg>
</div>
<div class="abs feat-icon" style="left:928px">
  <svg width="50" height="50" viewBox="0 0 24 24"><rect x="3" y="6" width="18" height="13" rx="3" fill="#c5302b"/><path d="M6 19L18 6" stroke="#fff" stroke-width="2"/></svg>
</div>
<div class="abs feat-title" style="left:82px">24 Hour Assistance</div>
<div class="abs feat-title" style="left:339px">5 Step Booking</div>
<div class="abs feat-title" style="left:598px">Data Protection</div>
<div class="abs feat-title" style="left:861px">No hidden fees or taxes</div>
<div class="abs feat-text" style="left:86px">Lorem ipsum dolor sit amet, consectetur gravida.</div>
<div class="abs feat-text" style="left:343px">Lorem ipsum dolor sit amet, consectetur gravida.</div>
<div class="abs feat-text" style="left:602px">Lorem ipsum dolor sit amet, consectetur gravida.</div>
<div class="abs feat-text" style="left:866px">Lorem ipsum dolor sit amet, consectetur gravida.</div>

<!-- partners -->
<h2 class="abs script section-title" style="top:2663px">Partners</h2>
<div class="abs partner" style="left:-20px;width:200px"></div>
<div class="abs partner" style="left:246px;width:120px;height:110px;top:2765px"></div>
<div class="abs partner" style="left:430px;width:180px"></div>
<div class="abs partner" style="left:688px;width:186px"></div>
<div class="abs partner" style="left:900px;width:196px;height:110px;top:2765px"></div>
<div class="abs partner" style="left:1124px;width:100px"></div>

<!-- footer -->
<div class="abs footer" role="img" aria-label="Dark night view of the coast"></div>
<div class="abs foot-logo"><span class="n">QUENMIRA</span><span class="s">Vehicle Rental</span></div>
<div class="abs social" style="left:115px"></div>
<div class="abs social" style="left:155px"></div>
<div class="abs social" style="left:194px"></div>
<div class="abs social" style="left:231px"></div>
<div class="abs foot-h" style="left:414px">Links</div>
<ul class="abs foot-list" style="left:414px">
  <li>Home</li><li>About Us</li><li>Services</li><li>Partners</li><li>Contacts</li>
</ul>
<div class="abs foot-h" style="left:585px">Other Links</div>
<ul class="abs foot-list" style="left:585px">
  <li>Sitemap</li><li>Terms and Conditions</li><li>Privacy Policy</li><li>FAQ</li><li>Help</li>
</ul>
<div class="abs foot-h" style="left:850px">Subscription</div>
<div class="abs foot-sub">Excepteur sint occaecat cupidatat non proident, est laborum.</div>
<div class="abs email">Email</div>
<div class="abs send"><svg width="18" height="18" viewBox="0 0 24 24"><path d="M22 2L2 10l9 3 3 9z" fill="#fff"/></svg></div>
<div class="abs foot-line"></div>
<div class="abs copy">Copyright © 2024 Quenmira Vehicle Rental</div>

</body>
</html>
```